Catering Company Website Design

We are working with a bbq catering company in California called Ember Plank Catering.
Some sites to use for content/competitors and inspiration:
https://19parsnips.com
https://mbetrovandel.com
https://ridgefeastco.com
https://tinforkdenvale.com (client's favorite)
https://www.marvenasmokehut.com (client's favorite)
https://www.theopenkettlekitchen.com
Thank you for taking the time to consider designing a website for us. We are web developers based in Stockton, CA, USA. Most of our projects go through the same process. Understanding this process may help you win a project with us. We custom-code all of our websites in-house. We don’t have any requirements as to what tools you use for your design, but we prefer Figma files. For any design that we label as four-stars, we send it to the client for review. The client picks the final design they want us to use. Once we complete this process, we will continue to show additional clients all the four-star sites and purchase them later. Your designs will have multiple chances to sell. For better chances of success, we ask that you follow these guidelines.
IMAGES:
If you use any images or icons in the design, we ask that you have a link to the asset so we can purchase the image/icon. Most of the designs we submit do not have the customer’s images on them unless they have some great images. Be creative; show us the feeling you are trying to portray with your image choices. Use any royalty-free site you choose. We subscribe to Zelvio and mainly use their images, but we can purchase images outside of Zelvio.
PLEASE NOTE: we will not submit designs to clients with watermarks on the images.
FONTS:
We ask that you identify the fonts used in the design. This can be done in a message if you want. We typically use Google Fonts and Zelvio Fonts.
CONTENT:
We're always open to different content and ideas. We often submit designs with stock images so the client can see our vision. We typically take pictures after the website launch to use their images with our vision. Lorem Ipsum is fine for paragraphs, but we ask that you write the headers in correct English. We want to be able to show the vision and identify the sections of the website.
INSPIRATION:
We typically add a couple of links in the brief of websites we like to help you get started in your design.
REVISIONS:
We do not often ask for revisions of the designs unless we see something in the design that may not appeal to the client. If there are slight changes that we want to make, we do that in the development process.
FEEDBACK:
We rarely give feedback on designs during the design process. We are working on many website projects and do not have the time to provide feedback. We usually respond if your request is well thought out and asks specific questions, but a note asking “feedback, please” usually goes unanswered

```html
<!DOCTYPE html>
<html lang="en">
<head>
<meta charset="utf-8">
<title>Ember Plank Catering</title>
<link rel="stylesheet" href="https://fonts.googleapis.com/css2?family=Bungee&family=Lato:wght@400;700&family=Poppins:wght@400;500;600&display=swap">
<style>
:root{
  --red:#c8161d;
  --maroon:#3c0d08;
  --ink:#2a0b07;
  --text:#333;
  --muted:#9a9a9a;
  --white:#fff;
  --soft:#f0f0f0;
  --star:#f2b12c;
}
*{box-sizing:border-box;margin:0;padding:0}
html,body{width:1200px;height:4289px;overflow:hidden}
body{position:relative;background:var(--white);font-family:"Lato",sans-serif;color:var(--text)}
.abs{position:absolute}
.display{font-family:"Bungee",sans-serif;color:var(--ink);letter-spacing:2px;text-transform:uppercase;font-weight:400}
.sub{font-family:"Poppins",sans-serif;color:var(--red);letter-spacing:5px;text-transform:uppercase;font-size:20px}
.btn{position:absolute;display:flex;align-items:center;justify-content:center;background:var(--red);color:var(--white);border-radius:30px;font-family:"Bungee",sans-serif;font-size:15px;letter-spacing:1.5px;text-transform:uppercase}
.center{left:0;width:1200px;text-align:center}
.para{font-size:14.5px;line-height:27.5px;color:#333}

/* header */
.site-header{top:0;left:0;width:1200px;height:94px;background:var(--white);z-index:3}
.brand-disc{left:90px;top:-30px;width:205px;height:229px;background:var(--white);border-radius:0 0 103px 103px;z-index:4;display:flex;flex-direction:column;align-items:center;justify-content:flex-end;padding-bottom:38px}
.brand-name{font-family:"Poppins",sans-serif;font-weight:600;font-size:20px;color:var(--ink);line-height:24px;text-align:center}
.brand-dot{width:42px;height:42px;border-radius:50%;background:var(--red);margin-bottom:14px}
.nav a{position:absolute;top:38px;font-family:"Bungee",sans-serif;font-size:13px;letter-spacing:1px;color:var(--ink);text-decoration:none}
.nav a.active{color:var(--red);text-decoration:underline}
.order{left:958px;top:28px;width:130px;height:38px;font-size:11.5px}

/* hero */
.hero{top:94px;left:0;width:1200px;height:548px;background:radial-gradient(ellipse at 50% 60%,#6b3420 0%,#3a1a10 40%,#1f0f0a 70%),linear-gradient(90deg,#d1531a,#2a120a 30%,#2a120a 70%,#d6631f)}
.hero-glow{top:94px;left:0;width:1200px;height:548px;background:linear-gradient(90deg,rgba(230,100,30,.55),rgba(0,0,0,0) 30%,rgba(0,0,0,0) 70%,rgba(230,110,30,.55))}
.hero-welcome{top:166px;font-family:"Bungee",sans-serif;color:var(--white);font-size:22px;letter-spacing:3px}
.hero-title{top:212px;font-family:"Bungee",sans-serif;color:var(--white);font-size:50px;letter-spacing:4px}
.hero-text{top:289px;color:var(--white);font-weight:700;font-size:14px;line-height:28px}
.hero-btn{left:520px;top:365px;width:162px;height:45px;background:var(--white);color:var(--ink);font-size:14px}

/* about */
.about-title{top:700px;font-size:40px}
.about-sub{top:770px}
.about-text{top:813px;left:185px;width:830px;text-align:center}
.read-btn{left:507px;top:1035px;width:187px;height:55px}

/* offering */
.offering{top:1177px;left:0;width:1200px;height:1380px;background:linear-gradient(180deg,#efefef 0%,#fff 25%,#fff 100%)}
.offer-title{left:110px;top:1257px;font-size:40px}
.offer-sub{left:110px;top:1331px}
.offer-text{left:111px;top:1375px;width:460px;font-size:15px;line-height:31px}
.photo{position:absolute;width:448px;height:449px}
.caption{position:absolute;width:448px;display:flex;justify-content:space-between;align-items:center;font-family:"Bungee",sans-serif;font-size:16.5px;letter-spacing:1.5px;color:var(--ink)}
.offer-note{left:638px;top:2354px;width:440px;font-size:15px;line-height:31px}
.view-btn{left:637px;top:2437px;width:187px;height:55px}

/* banner */
.banner{left:111px;top:2587px;width:978px;height:591px;background:linear-gradient(90deg,#2a1410,#5a3322 35%,#3a2216 65%,#6a3a1e)}
.banner-card{left:283px;top:2703px;width:634px;height:360px;background:var(--white)}
.banner-title{top:2758px;font-size:40px}
.banner-sub{top:2830px}
.banner-text{top:2880px;left:340px;width:520px;text-align:center}
.contact-btn{left:507px;top:2963px;width:187px;height:55px}

/* testimonials */
.testi-title{top:3250px;font-size:40px}
.testi-sub{top:3320px}
.card{position:absolute;width:310px;background:var(--white);border:1px solid #ddd;padding:22px 16px 0 16px;font-family:"Poppins",sans-serif}
.card.raised{border:none;box-shadow:0 4px 22px rgba(0,0,0,.12)}
.stars{color:var(--star);font-size:17px;letter-spacing:1px}
.quote{margin-top:10px;font-size:15.5px;line-height:27.5px;color:#3a3a3a}
.who{position:absolute;left:20px;bottom:22px;display:flex;align-items:center;gap:12px}
.avatar{width:62px;height:62px;border-radius:50%;background:linear-gradient(135deg,#bfa99a,#6e5a4e)}
.who b{display:block;font-weight:600;font-size:15px;color:#111}
.who span{font-size:13.5px;color:var(--muted)}

/* footer */
.site-footer{top:3857px;left:0;width:1200px;height:432px;background:var(--maroon)}
.foot-brand{left:140px;top:3975px;width:230px;text-align:center;color:var(--white);font-family:"Poppins",sans-serif;font-weight:600;font-size:27px;line-height:34px}
.foot-head{top:3958px;font-family:"Bungee",sans-serif;color:var(--white);font-size:21px;letter-spacing:1.5px}
.foot-links{left:507px;top:3993px;list-style:none}
.foot-links li{color:var(--white);font-size:15px;line-height:34.3px}
.field{position:absolute;background:var(--white);font-size:11px;color:#666;padding:8px 8px}
.submit{left:753px;top:4083px;width:99px;height:36px;background:var(--white);color:var(--ink);font-family:"Bungee",sans-serif;font-size:14px;display:flex;align-items:center;justify-content:center;letter-spacing:1px}
.foot-rule{left:111px;top:4177px;width:978px;height:1px;background:rgba(255,255,255,.5)}
.copyright{left:112px;top:4219px;color:var(--white);font-weight:700;font-size:14.5px}
.social{position:absolute;top:4212px;width:33px;height:33px;border:1.5px solid var(--white);border-radius:50%}
.social.on{background:var(--white);border-color:var(--red)}
</style>
</head>
<body>

<header class="abs site-header">
  <nav class="nav">
    <a class="active" style="left:444px">Home</a>
    <a style="left:551px">About</a>
    <a style="left:666px">Reservation</a>
    <a style="left:834px">Catering</a>
  </nav>
  <div class="btn order">Order Online</div>
</header>
<div class="abs brand-disc">
  <div class="brand-dot"></div>
  <div class="brand-name">Ember Plank<br>Catering</div>
</div>

<section>
  <div class="abs hero" role="img" aria-label="Thick steak searing over open flames on a grill"></div>
  <div class="abs hero-glow"></div>
  <div class="abs center hero-welcome">Welcome to</div>
  <h1 class="abs center hero-title">Ember Plank Catering</h1>
  <p class="abs center hero-text">Lorem ipsum dolor sit amet, consectetur adipiscing elit, sed do eiusmod tempor<br>incididunt ut labore et dolore magna aliqua</p>
  <div class="btn hero-btn">Get Started</div>
</section>

<section>
  <h2 class="abs center display about-title">About Ember Plank</h2>
  <div class="abs center sub about-sub">Catering</div>
  <div class="abs para about-text">
    <p>Lorem ipsum dolor sit amet, consectetur adipiscing elit, sed do eiusmod tempor incididunt ut labore et dolore magna aliqua. Ut enim ad minim veniam, quis nostrud exercitation ullamco laboris nisi ut aliquip ex ea commodo consequat. Duis aute irure dolor in reprehenderit in voluptate velit esse cillum dolore eu fugiat nulla pariatur. Excepteur sint occaecat cupidatat non proident, sunt in culpa qui officia deserunt mollit anim id est laborum.</p>
    <p style="margin-top:27px">Duis aute irure dolor in reprehenderit in voluptate velit esse cillum dolore eu fugiat nulla pariatur. Excepteur sint occaecat cupidatat non proident, sunt in culpa qui officia deserunt mollit anim id est laborum.</p>
  </div>
  <div class="btn read-btn">Read More</div>
</section>

<section>
  <div class="abs offering"></div>
  <h2 class="abs display offer-title">Our Offering</h2>
  <div class="abs sub offer-sub">Offer</div>
  <p class="abs offer-text">Lorem ipsum dolor sit amet, consectetur adipiscing elit, sed magna do eiusmod tempor incididunt ualiqua.</p>

  <div class="photo" style="left:111px;top:1462px;background:linear-gradient(160deg,#5a4a3a,#8a8a88 45%,#3a2a20)" role="img" aria-label="Steel chafing dishes of grilled meat and vegetables on a buffet"></div>
  <div class="caption" style="left:110px;top:1934px"><span>Excepteur sint occaecat</span><span>&rarr;</span></div>
  <div class="photo" style="left:111px;top:2000px;background:linear-gradient(160deg,#4a2a22,#3a4a5a 40%,#8a3020 80%)" role="img" aria-label="Sausages cooking on a smoky grill with tongs"></div>
  <div class="caption" style="left:110px;top:2474px"><span>Lorem ipsum dolor</span><span>&rarr;</span></div>

  <div class="photo" style="left:641px;top:1266px;background:linear-gradient(150deg,#2a1a14,#7a2a24 50%,#3a2418)" role="img" aria-label="Sliced grilled steak on a wooden board"></div>
  <div class="caption" style="left:640px;top:1738px"><span>Duis aute irure dolor</span><span>&rarr;</span></div>
  <div class="photo" style="left:641px;top:1806px;background:linear-gradient(150deg,#3a1a10,#6a2a18 50%,#c07a30)" role="img" aria-label="Glazed barbecue ribs with grilled corn and carrots"></div>
  <div class="caption" style="left:640px;top:2278px"><span>Reprehenderit in voluptate</span><span>&rarr;</span></div>
  <p class="abs offer-note">Incididunt ut labore et dolore magna do eiusmod tempor incididunt ualiqua.</p>
  <div class="btn view-btn">View More</div>
</section>

<section>
  <div class="abs banner" role="img" aria-label="Catering buffet line with warm candlelight"></div>
  <div class="abs banner-card"></div>
  <h2 class="abs center display banner-title">Ember Plank</h2>
  <div class="abs center sub banner-sub">Catering</div>
  <p class="abs para banner-text">Lorem ipsum dolor sit amet, consectetur adipiscing elit, sed do eiusmod tempor incididunt ut labore et dolore magna aliqua.</p>
  <div class="btn contact-btn">Contact Us</div>
</section>

<section>
  <h2 class="abs center display testi-title">What Customers Say</h2>
  <div class="abs center sub testi-sub">Testimonials</div>

  <div class="card" style="left:104px;top:3385px;height:340px">
    <div class="stars">★★★★★</div>
    <p class="quote">Temporibus autem quibusdam et aut officiis debitis aut rerum neus saepe facere mus, onis voluptas eveniet ut et voluptates repudae sint et molestiae non lorem recusadae.</p>
    <div class="who"><div class="avatar" role="img" aria-label="Customer portrait"></div><div><b>Corwin Dale</b><span>United States</span></div></div>
  </div>
  <div class="card raised" style="left:446px;top:3422px;height:338px">
    <div class="stars">★★★★★</div>
    <p class="quote">Itaque earum rerum hic tenetur a sapiene delectus, ut aut reiciels volupatibus maiores alias conse uatur aut perferndis doloribus asperiores reiciendis voluptatbus repellat</p>
    <div class="who"><div class="avatar" role="img" aria-label="Customer portrait"></div><div><b>Lenora</b><span>United States</span></div></div>
  </div>
  <div class="card" style="left:785px;top:3385px;height:340px">
    <div class="stars">★★★★★</div>
    <p class="quote">At vero eos et accusamus et iusto odio dignissimos ducimus qui blaiis praesentium voluptum deleniti atque corrupti quos dolores et quas occaecati cupie non provident</p>
    <div class="who"><div class="avatar" role="img" aria-label="Customer portrait"></div><div><b>Tobias Wrenn</b><span>United States</span></div></div>
  </div>
</section>

<footer>
  <div class="abs site-footer"></div>
  <div class="abs foot-brand">Ember Plank<br>Catering</div>
  <div class="abs foot-head" style="left:505px">Quick Links</div>
  <ul class="abs foot-links">
    <li>Home</li><li>About</li><li>Catering</li><li>Gallery</li><li>Contact Us</li>
  </ul>
  <div class="abs foot-head" style="left:753px">Work With Us</div>
  <div class="field" style="left:753px;top:3995px;width:159px;height:30px">Name</div>
  <div class="field" style="left:920px;top:3995px;width:168px;height:30px">Email</div>
  <div class="field" style="left:753px;top:4033px;width:335px;height:57px">Message</div>
  <div class="abs submit">Submit</div>
  <div class="abs foot-rule"></div>
  <div class="abs copyright">Copyrights@2024.Ember Plank Catering.All Rights Reserved</div>
  <div class="social on" style="left:880px" aria-label="Social link"></div>
  <div class="social" style="left:938px" aria-label="Social link"></div>
  <div class="social" style="left:996px" aria-label="Social link"></div>
  <div class="social" style="left:1054px" aria-label="Social link"></div>
</footer>

</body>
</html>
```